Beautiful design for wordpress

I need a beautiful, colourful and feminine website. My business is called 'The Velvet Lantern', and I sell crystals, books, CD's, pendulums and other metaphysical items. I also provide Reiki (energy healing).
I want this design to be eye catching and inspire happiness and joy in those who see it. And I would love to see the use of the logo and its colours :)
Please add these on the web design: Home, About, Online store, Blog

Industry/Entity Type

Business

Requirements
Must have
• Colourful and playful, must use the logo somewhere, have the words on a menu saying 'Home, Blog, Online store and about' (or similar to those)And the design must stand out!
Should not have
• grey, brown and other boring colours.

```html
<!DOCTYPE html>
<html lang="en">
<head>
<meta charset="utf-8">
<title>The Velvet Lantern – Crystals &amp; Gifts</title>
<link href="https://fonts.googleapis.com/css2?family=Amatic+SC:wght@700&family=Open+Sans:wght@400;700&display=swap" rel="stylesheet">
<style>
:root{
  --pink:#f73cb5;
  --pink-dark:#d8249a;
  --salmon:#fb7f8a;
  --orange:#fba74a;
  --lime:#a7cc3a;
  --paper:#f4f4f3;
  --frame:#9c9c9c;
  --text:#5a5a5a;
  --heading:#4d4d4d;
  --white:#ffffff;
}
*{box-sizing:border-box;margin:0;padding:0}
html,body{width:1130px;height:1200px;overflow:hidden}
body{background:var(--paper);font-family:'Open Sans',Arial,sans-serif;color:var(--text);position:relative}
.display{font-family:'Amatic SC',cursive}
.top-stripe{position:absolute;top:0;left:0;width:1130px;height:6px;display:flex}
.top-stripe span{flex:1}
.brand{position:absolute;left:68px;top:60px;width:190px;display:flex;align-items:center;gap:10px;color:var(--heading);font-weight:700;font-size:26px;line-height:1.1}
.brand-dot{width:22px;height:22px;border-radius:50%;background:var(--pink);flex:none}
.brand-tag{position:absolute;left:100px;top:196px;font-size:9px;letter-spacing:2px;font-weight:700;color:var(--heading)}
.search{position:absolute;left:274px;top:101px;width:318px;height:35px;border:3px solid #c9c9c9;border-radius:8px;background:var(--white);display:flex;overflow:hidden}
.search span{flex:1;padding:5px 12px;font-size:14px;color:#555}
.search-btn{width:42px;background:var(--lime);display:flex;align-items:center;justify-content:center}
.cart{position:absolute;left:930px;top:129px;font-size:14px;color:#555;display:flex;align-items:center;gap:5px}
.nav{position:absolute;left:277px;top:156px;width:768px;height:47px;background:var(--pink);clip-path:polygon(0 0,100% 0,100% 100%,0 100%,12px 50%);display:flex;align-items:center;padding-left:26px}
.nav a{color:var(--white);text-decoration:none;font-weight:700;font-size:14px;padding:0 22px;height:31px;line-height:31px;border-right:2px dashed rgba(255,255,255,.55)}
.nav a:first-child{border-left:2px dashed rgba(255,255,255,.55)}
.nav-tail{position:absolute;left:1030px;top:178px}
.hero{position:absolute;left:66px;top:247px;width:657px;height:326px;border:3px solid var(--frame)}
.photo{position:absolute;inset:0}
.hero-title{position:absolute;left:-8px;top:21px;background:var(--pink);color:var(--white);font-size:56px;line-height:60px;padding:0 10px}
.hero-copy{position:absolute;left:10px;top:96px;width:190px;font-size:14px;line-height:20px;color:var(--white)}
.hero-copy span{background:rgba(120,110,100,.6);padding:1px 3px;box-decoration-break:clone;-webkit-box-decoration-break:clone}
.btn{display:inline-block;color:var(--white);font-weight:700;font-size:14px;border-radius:7px;padding:9px 13px;box-shadow:0 3px 0 rgba(0,0,0,.15)}
.btn-pink{background:var(--pink)}
.btn-salmon{background:var(--salmon)}
.btn-orange{background:var(--orange)}
.hero .btn{position:absolute;left:9px;top:212px}
.dots{position:absolute;left:365px;top:582px;display:flex;gap:7px}
.dots i{width:11px;height:11px;border-radius:50%;border:1.5px solid #8a8a8a;display:block}
.dots i:first-child{background:#8a8a8a}
.promo{position:absolute;left:754px;width:311px;height:147px;border:3px solid var(--frame);background:var(--white)}
.promo .photo{right:auto}
.promo-tag{position:absolute;right:-8px;top:18px;background:var(--pink);color:var(--white);font-size:36px;line-height:40px;padding:0 8px}
.promo-offer{position:absolute;right:10px;top:66px;text-align:right;font-size:38px;line-height:36px;color:#555}
.promo-offer small{display:block;font-family:'Open Sans',Arial,sans-serif;font-size:14px;line-height:20px;color:#555}
.ribbon{position:absolute;top:629px;width:311px;height:48px;color:var(--white);font-weight:700;font-size:14px;display:flex;align-items:center;justify-content:center;clip-path:polygon(0 0,100% 0,94% 50%,100% 100%,0 100%,6% 50%)}
.col{position:absolute;top:700px}
.post-title{font-size:40px;line-height:44px;color:var(--heading)}
.post-text{font-size:14px;line-height:20px;width:270px;margin-top:6px}
.post-date{font-size:14px;font-weight:700;color:var(--pink);margin-top:12px}
.rule{width:270px;border-top:2px dashed #555;margin:26px 0 22px}
.products{position:absolute;left:423px;top:697px;display:grid;grid-template-columns:repeat(3,77px);gap:20px 21px}
.thumb{width:77px;height:77px;border:2px solid var(--orange);padding:3px;background:var(--white)}
.thumb div{width:100%;height:100%}
.about{position:absolute;left:767px;top:694px;width:300px;font-size:14px;line-height:20px}
.about p{margin-bottom:20px}
.footer{position:absolute;left:0;top:1136px;width:1130px;height:64px;background:var(--lime);display:flex;align-items:center;padding:0 66px;justify-content:space-between}
.footer .display{color:var(--white);font-size:38px}
.social{display:flex;gap:12px}
.social i{display:block;width:41px;height:41px;border-radius:50%;background:rgba(255,255,255,.35)}
</style>
</head>
<body>
<div class="top-stripe"><span style="background:var(--pink)"></span><span style="background:var(--salmon)"></span><span style="background:var(--orange)"></span><span style="background:var(--lime)"></span><span style="background:var(--pink)"></span></div>

<header>
  <div class="brand"><span class="brand-dot"></span><span>The Velvet Lantern</span></div>
  <div class="brand-tag">CRYSTALS &amp; GIFTS</div>
  <div class="search"><span>Search</span><div class="search-btn"><svg width="18" height="18" viewBox="0 0 18 18"><circle cx="7.5" cy="7.5" r="5.5" fill="none" stroke="#fff" stroke-width="2.6"/><line x1="11.5" y1="11.5" x2="16" y2="16" stroke="#fff" stroke-width="3" stroke-linecap="round"/></svg></div></div>
  <div class="cart"><span style="display:inline-block;width:10px;height:10px;border-radius:50%;background:var(--pink)"></span>My Cart
    <svg width="15" height="13" viewBox="0 0 15 13"><path d="M0 1h3l2 7h8l2-6H4" fill="none" stroke="#555" stroke-width="1.6"/><circle cx="6" cy="11" r="1.4" fill="#555"/><circle cx="12" cy="11" r="1.4" fill="#555"/></svg>(0)</div>
  <nav class="nav"><a>HOME</a><a>ABOUT</a><a>ONLINE STORE</a><a>BLOG</a><a>CONTACT US</a></nav>
  <svg class="nav-tail" width="36" height="50" viewBox="0 0 36 50"><polygon points="0,0 30,0 22,20 36,48 0,25" fill="var(--pink-dark)"/></svg>
</header>

<section class="hero">
  <div class="photo" role="img" aria-label="Stacked grey stones on a rock before a soft blurred colourful background" style="background:radial-gradient(ellipse at 50% 55%,#8b8f96 0,#a8a6a0 22%,transparent 40%),linear-gradient(120deg,#e8c98a,#f2d7a0 35%,#c7a7c4 65%,#a8b47a)"></div>
  <div class="hero-title display">Reiki Healing</div>
  <p class="hero-copy"><span>Marzipan croissant tiramisu cookie. Chocolate ice cream cheesecake cotton candy cupcake fruitcake.</span></p>
  <span class="btn btn-pink">READ MORE</span>
</section>
<div class="dots"><i></i><i></i><i></i></div>

<aside class="promo" style="top:247px">
  <div class="photo" role="img" aria-label="Silver cat figurine" style="width:100px;background:linear-gradient(160deg,#d8d8d8,#8d8d8d 60%,#bdbdbd)"></div>
  <div class="promo-tag display">Fruitcake Jelly</div>
  <div class="promo-offer display">50% off*<small>*danish marzipan</small></div>
</aside>
<aside class="promo" style="top:426px">
  <div class="photo" role="img" aria-label="Clear quartz crystal cluster on green" style="width:100%;background:linear-gradient(120deg,#7fae3c,#5d8f4a 40%,#5a7a7a 70%,#3f5f5f)"></div>
  <div class="promo-tag display">Reiki Healing</div>
</aside>

<div class="ribbon" style="left:66px;background:var(--salmon)">LATEST BLOG POSTS</div>
<div class="ribbon" style="left:410px;background:var(--orange)">OUR PRODUCTS</div>
<div class="ribbon" style="left:754px;background:var(--salmon)">ABOUT THE VELVET LANTERN</div>

<section class="col" style="left:85px">
  <article>
    <h2 class="post-title display">Candy toffee cake jelly.</h2>
    <p class="post-text">Sweet candy canes tiramisu cake gummi bears cookie sweet roll caramels chupa chups donut […]</p>
    <p class="post-date">Posted on: 23 May 2014</p>
  </article>
  <div class="rule"></div>
  <article>
    <h2 class="post-title display">Tiramisu gummi bears.</h2>
    <p class="post-text">Sweet candy canes tiramisu cake gummi bears cookie sweet roll caramels chupa chups donut […]</p>
    <p class="post-date">Posted on: 23 May 2014</p>
  </article>
  <div class="rule"></div>
  <span class="btn btn-salmon" style="margin-left:164px">READ MORE</span>
</section>

<section class="products">
  <div class="thumb"><div role="img" aria-label="Purple crystal ball" style="background:radial-gradient(circle at 45% 40%,#c9a3ef,#7a3fc4 55%,#fff 72%)"></div></div>
  <div class="thumb"><div role="img" aria-label="Music CD" style="background:radial-gradient(circle,#fff 10%,#d6d6d6 45%,#f4f4f4 70%)"></div></div>
  <div class="thumb"><div role="img" aria-label="Silver cat figurine" style="background:linear-gradient(160deg,#ddd,#8f8f8f 60%,#f0f0f0)"></div></div>
  <div class="thumb"><div role="img" aria-label="Cream pillar candle" style="background:linear-gradient(180deg,#f3ecde,#e3d6bd)"></div></div>
  <div class="thumb"><div role="img" aria-label="Red book" style="background:linear-gradient(135deg,#e4453f,#b8231f)"></div></div>
  <div class="thumb"><div role="img" aria-label="Quartz crystal cluster" style="background:linear-gradient(120deg,#7fae3c,#4f7a6c)"></div></div>
</section>
<span class="btn btn-orange" style="position:absolute;left:582px;top:893px">BROWSE STORE</span>

<section class="about">
  <p>The Velvet Lantern sells crystals, books, CD's, pendulums and other metaphysical items. I also provide Reiki.</p>
  <p>Cookie lollipop powder lemon drops. Toffee bear claw marshmallow tart gingerbread applicake. Tiramisu gummies danish chocolate bar macaroon.</p>
  <p>Jujubes jelly beans muffin. Chupa chups fruitcake lemon drops danish. Sesame snaps cookie caramels.</p>
</section>
<span class="btn btn-salmon" style="position:absolute;left:949px;top:947px">READ MORE</span>

<footer class="footer">
  <span class="display">© 2014 The Velvet Lantern</span>
  <div class="social"><i></i><i></i><i></i><i></i></div>
</footer>
</body>
</html>
```